Business Card Design for Flood Rescue 360 - Property Restoration Professionals

I need a business card designed for Flood Rescue 360. We are a full-service property restoration solution. Providing water, fire, smoke & storm restoration as well as mold remediation and full remodel or reconstruction to homes and businesses across Dallas-Fort Worth, TX.
Target Market(s)
home and business owners with insurance covered property damage from water, fire or storm related damage
Industry/Entity Type
property restoration
Contact Information for Business Card
Marcus Pelley General Manager Cell: 214-555-0193 Office: 469-555-0148 email: Marcus@FloodRescue360.example services: Water, Fire, Mold, Reconstruction Tagline: Urgency for Your Water Emergency!
Look and feel
Each slider illustrates characteristics of the customer's brand and the style your logo design should communicate.

```html
<!DOCTYPE html>
<html lang="en">
<head>
<meta charset="utf-8">
<title>Flood Rescue 360 – Business Card</title>
<link rel="stylesheet" href="https://fonts.googleapis.com/css2?family=Montserrat:wght@400;500;800&display=swap">
<style>
  :root {
    --bg: #4a4a4a;
    --card: #161616;
    --brand-blue: #14b3e6;
    --text-light: #f2f2f2;
    --text-muted: #c9c9c9;
    --emboss: #2a2a2a;
  }
  * { box-sizing: border-box; margin: 0; padding: 0; }
  html, body {
    width: 1200px; height: 801px; overflow: hidden;
    background: var(--bg);
    font-family: "Montserrat", sans-serif;
  }
  .sheet {
    width: 1200px; height: 801px;
    display: flex; align-items: center; justify-content: center; gap: 40px;
  }
  .card {
    position: relative;
    width: 540px; height: 309px;
    background: var(--card);
    border-bottom: 3px solid var(--brand-blue);
    overflow: hidden;
  }

  /* Front */
  .card-front { padding: 26px 28px; color: var(--text-light); }
  .brand {
    display: flex; align-items: center; gap: 8px;
    color: var(--brand-blue); font-weight: 800; font-size: 20px;
    text-transform: uppercase; letter-spacing: 0.5px; line-height: 1;
  }
  .brand-dot {
    width: 14px; height: 14px; border-radius: 50%;
    background: var(--brand-blue);
  }
  .person { margin-top: 24px; }
  .person-name { color: var(--brand-blue); font-weight: 800; font-size: 24px; line-height: 1.1; }
  .person-title { font-size: 13px; font-weight: 400; margin-top: 4px; }
  .tagline { font-size: 12.5px; margin-top: 16px; }
  .contacts { list-style: none; margin-top: 14px; }
  .contacts li {
    display: flex; align-items: center; gap: 8px;
    font-size: 12.5px; line-height: 1.55;
  }
  .contacts svg { width: 12px; height: 12px; flex: none; }

  .services {
    position: absolute; top: 26px; right: 28px;
    text-align: right;
  }
  .services-heading {
    color: var(--brand-blue); font-weight: 800; font-size: 20px;
    letter-spacing: 0.5px; margin-bottom: 6px;
  }
  .services-list { list-style: none; }
  .services-list li {
    display: flex; align-items: center; justify-content: flex-end; gap: 6px;
    font-size: 13px; line-height: 1.6;
  }
  .services-list li::after {
    content: ""; width: 8px; height: 8px; border-radius: 50%;
    border: 1.5px solid var(--brand-blue);
  }

  /* Back */
  .card-back {
    display: flex; align-items: center; justify-content: center; gap: 18px;
  }
  .back-name {
    color: var(--emboss); font-weight: 800; font-size: 44px;
    text-transform: uppercase; line-height: 1.02; letter-spacing: 1px;
  }
  .back-mark {
    width: 70px; height: 70px; border-radius: 50%;
    border: 8px solid var(--emboss);
  }
</style>
</head>
<body>
<main class="sheet">
  <section class="card card-front" aria-label="Business card front">
    <div class="brand"><span class="brand-dot"></span>Flood Rescue 360</div>

    <div class="person">
      <h1 class="person-name">Marcus Pelley</h1>
      <p class="person-title">General Manager</p>
    </div>

    <p class="tagline">Urgency for Your Water Emergency!</p>

    <ul class="contacts">
      <li>
        <svg viewBox="0 0 12 12" aria-hidden="true"><rect x="3" y="1" width="6" height="10" rx="1" fill="none" stroke="#14b3e6" stroke-width="1.2"/></svg>
        214-555-0193
      </li>
      <li>
        <svg viewBox="0 0 12 12" aria-hidden="true"><path d="M2 4 Q6 1 10 4 L9 6 L7 5 L5 5 L3 6 Z" fill="#14b3e6"/><rect x="3" y="7" width="6" height="4" fill="#14b3e6"/></svg>
        469-555-0148
      </li>
      <li>
        <svg viewBox="0 0 12 12" aria-hidden="true"><rect x="1" y="3" width="10" height="7" fill="none" stroke="#14b3e6" stroke-width="1.2"/><path d="M1 3 L6 7 L11 3" fill="none" stroke="#14b3e6" stroke-width="1.2"/></svg>
        Marcus@FloodRescue360.example
      </li>
      <li>
        <svg viewBox="0 0 12 12" aria-hidden="true"><circle cx="6" cy="6" r="5" fill="none" stroke="#14b3e6" stroke-width="1.2"/><path d="M1 6 H11 M6 1 Q3 6 6 11 M6 1 Q9 6 6 11" fill="none" stroke="#14b3e6" stroke-width="1"/></svg>
        FloodRescue360.example
      </li>
    </ul>

    <div class="services">
      <h2 class="services-heading">SERVICES</h2>
      <ul class="services-list">
        <li>Water</li>
        <li>Fire</li>
        <li>Mold</li>
        <li>Reconstruction</li>
      </ul>
    </div>
  </section>

  <section class="card card-back" aria-label="Business card back">
    <p class="back-name">Flood<br>Rescue 360</p>
    <span class="back-mark" aria-hidden="true"></span>
  </section>
</main>
</body>
</html>
```